Professional Coaching Business Letterhead/Footer

I need a letterhead and email footer for my personal coaching business, Dorian K Whitfield Professional Coaching. I send several attachments to new clients (such as welcome letter, fee structure, etc) and would like these pages to have my branding on them.
I prefer the black and gold/silver color scheme, and will attach my logo to be used. I'd like the overall impression to be upmarket/regal/professional.

One of the uploaded files is my business card, to give an idea of the style/feel I like. The others are vector files containing logo to be used.

Target Market(s)

Corporate managers, successful business people. 30-60 yrs old.

Industry/Entity Type

Business

Requirements
Must have
• Logo (DKW)
Nice to have
• Shield emblem around logo, some type of watermark.
Should not have
• The first uploaded file is my business card, intended to show style and colors- not to be used itself as the letterhead.

```html
<!DOCTYPE html>
<html lang="en">
<head>
<meta charset="utf-8">
<title>Dorian K Whitfield Professional Coaching — Letterhead</title>
<link rel="stylesheet" href="https://fonts.googleapis.com/css2?family=Oswald:wght@400;500&display=swap">
<style>
  :root {
    --backdrop: #ffffff;
    --sheet-dark: #080808;
    --sheet-mid: #1c1c1c;
    --gold: #f0a818;
    --silver: #d6d6d6;
    --white: #f4f4f4;
  }
  html, body {
    margin: 0;
    padding: 0;
    width: 1200px;
    height: 1000px;
    overflow: hidden;
    background: var(--backdrop);
  }
  .canvas {
    position: relative;
    width: 1200px;
    height: 1000px;
  }
  .letterhead {
    position: absolute;
    left: 229px;
    top: 20px;
    width: 743px;
    height: 962px;
    overflow: hidden;
    background: radial-gradient(ellipse 70% 55% at 55% 35%, var(--sheet-mid) 0%, #121212 55%, var(--sheet-dark) 100%);
  }
  .brand {
    position: absolute;
    left: 42px;
    top: 58px;
    width: 150px;
    text-align: center;
  }
  .brand-circle {
    display: block;
    margin: 0 auto;
  }
  .brand-name {
    margin-top: 6px;
    font-family: "Oswald", sans-serif;
    font-weight: 400;
    font-size: 12px;
    letter-spacing: 1px;
    color: var(--silver);
    text-transform: uppercase;
    white-space: nowrap;
  }
  .footer {
    font-family: "Oswald", sans-serif;
    font-weight: 500;
    text-transform: uppercase;
    position: absolute;
  }
  .footer-left {
    left: 22px;
    top: 918px;
    display: flex;
    align-items: center;
    font-size: 21px;
    line-height: 1;
    letter-spacing: -0.3px;
  }
  .tagline { color: var(--gold); }
  .divider {
    width: 2px;
    height: 36px;
    background: var(--white);
    margin: 0 10px;
  }
  .phone { color: var(--white); }
  .footer-right {
    right: 30px;
    top: 917px;
    text-align: right;
    color: var(--gold);
    font-size: 15.5px;
    line-height: 20px;
  }
  .email { text-transform: none; }
</style>
</head>
<body>
<div class="canvas">
  <div class="letterhead" role="img" aria-label="Black letterhead sheet with a fine dark hexagonal texture">
    <div class="brand">
      <svg class="brand-circle" width="86" height="86" viewBox="0 0 86 86" aria-hidden="true">
        <circle cx="43" cy="43" r="40" fill="none" stroke="var(--silver)" stroke-width="3"/>
      </svg>
      <div class="brand-name">Dorian K Whitfield</div>
    </div>

    <div class="footer footer-left">
      <span class="tagline">Professional Coaching</span>
      <span class="divider"></span>
      <span class="phone">Phone : 555.014.2760</span>
    </div>

    <div class="footer footer-right">
      <div class="website">DORIANWHITFIELD.COM</div>
      <div class="email">dorian@DORIANWHITFIELD.COM</div>
    </div>
  </div>
</div>
</body>
</html>
```